The Linen Loft Co

We need a business card design for our wardrobe company.
Please visit our website www.gentlelinenlofts.com to get an idea of who we are.

```html
<!DOCTYPE html>
<html lang="en">
<head>
<meta charset="utf-8">
<title>The Linen Loft Co – Business Card</title>
<link rel="stylesheet" href="https://fonts.googleapis.com/css2?family=Roboto:wght@400;500;700&display=swap">
<style>
  :root {
    --backdrop: #d9d9d9;
    --card: #ffffff;
    --ink: #111111;
    --body-text: #3a3a3a;
    --muted: #a3a3a3;
    --band: #000000;
  }
  * { margin: 0; padding: 0; box-sizing: border-box; }
  html, body {
    width: 1200px;
    height: 989px;
    overflow: hidden;
    background: var(--backdrop);
    font-family: "Roboto", Arial, sans-serif;
  }
  .business-card {
    position: absolute;
    left: 164px;
    top: 226px;
    width: 884px;
    height: 512px;
    background: var(--card);
  }
  .bottom-band {
    position: absolute;
    left: 0;
    right: 0;
    bottom: 0;
    height: 18px;
    background: var(--band);
  }
  .brand-square {
    position: absolute;
    left: 60px;
    top: 64px;
    width: 80px;
    height: 80px;
    background: var(--ink);
  }
  .brand-name {
    position: absolute;
    left: 223px;
    top: 72px;
    font-size: 26px;
    font-weight: 500;
    color: var(--ink);
    line-height: 1;
    white-space: nowrap;
  }
  .brand-tagline {
    position: absolute;
    left: 248px;
    top: 108px;
    font-size: 20px;
    font-weight: 500;
    color: var(--ink);
    line-height: 1;
    white-space: nowrap;
  }
  .contact {
    position: absolute;
    left: 54px;
    top: 306px;
    color: var(--body-text);
    font-size: 22px;
    line-height: 27px;
  }
  .contact-address { margin-bottom: 10px; }
  .contact-row {
    display: flex;
    align-items: center;
    gap: 11px;
    height: 27px;
    margin-left: 0;
  }
  .contact-icon {
    width: 19px;
    height: 19px;
    flex: none;
  }
  .person {
    position: absolute;
    right: 48px;
    top: 354px;
    text-align: right;
  }
  .person-name {
    font-size: 38px;
    font-weight: 700;
    color: var(--ink);
    line-height: 1.05;
  }
  .person-role {
    font-size: 24px;
    font-weight: 500;
    color: var(--muted);
    line-height: 1.1;
  }
</style>
</head>
<body>
  <section class="business-card">
    <div class="brand-square"></div>
    <div class="brand-name">THE LINEN LOFT CO</div>
    <div class="brand-tagline">Crafted to Fit Every Room</div>

    <div class="contact">
      <p class="contact-address">Orchard House, 42 Mill Lane,<br>London N4 3QP</p>
      <div class="contact-row">
        <svg class="contact-icon" viewBox="0 0 24 24" aria-hidden="true">
          <path fill="#111" d="M6.6 10.8a15.1 15.1 0 0 0 6.6 6.6l2.2-2.2c.3-.3.7-.4 1-.2 1.1.4 2.3.6 3.6.6.6 0 1 .4 1 1V20c0 .6-.4 1-1 1A17 17 0 0 1 3 4c0-.6.4-1 1-1h3.5c.6 0 1 .4 1 1 0 1.3.2 2.5.6 3.6.1.3 0 .7-.2 1l-2.3 2.2z"/>
        </svg>
        <span>020 7946 0318</span>
      </div>
      <div class="contact-row">
        <svg class="contact-icon" viewBox="0 0 24 24" aria-hidden="true">
          <rect x="2" y="6" width="20" height="13" fill="#111"/>
          <path d="M3 7l9 7 9-7" fill="none" stroke="#fff" stroke-width="1.6"/>
          <path d="M3 18l7-6M21 18l-7-6" fill="none" stroke="#fff" stroke-width="1.2"/>
        </svg>
        <span>info@gentlelinenlofts.com</span>
      </div>
      <div class="contact-row">
        <svg class="contact-icon" viewBox="0 0 24 24" aria-hidden="true">
          <circle cx="12" cy="12" r="10" fill="#111"/>
          <path d="M7 6c2 0 3 1 3 3s-2 2-2 4 2 2 2 4-1 2-2 2M15 5c0 2 1 3 3 3s2 2 1 4" fill="none" stroke="#fff" stroke-width="1.6"/>
        </svg>
        <span>www.gentlelinenlofts.com</span>
      </div>
    </div>

    <div class="person">
      <div class="person-name">Daniel Hart</div>
      <div class="person-role">President</div>
    </div>

    <div class="bottom-band"></div>
  </section>
</body>
</html>
```